Law Offices business card

Hi there, I'll need business card for the Law Offices of Colin Matheny. The information must convey his strategic approach and quick resolution to complex business litigation needs. Please emphasize Civil Litigation, Corporate Law, Business Governance and Real Estate Law. Colin has over 25 years of experience in these fields.The card should be modern and edgy and the message should be clear. Please consult his current website for ideas.

```html
<!DOCTYPE html>
<html lang="en">
<head>
<meta charset="utf-8">
<title>Law Offices of Colin Matheny — Business Card</title>
<link rel="stylesheet" href="https://fonts.googleapis.com/css2?family=Tinos:wght@400;700&family=Open+Sans:wght@400;600&display=swap">
<style>
  :root {
    --page: #e9e6e1;
    --ink: #111111;
    --paper: #ffffff;
    --paper-shade: #f1f1f1;
    --band: #0c0c0c;
    --muted: #555555;
    --rule: #333333;
    --light-text: #f4f4f4;
    --light-rule: #9a9a9a;
  }
  * { box-sizing: border-box; margin: 0; padding: 0; }
  html, body { width: 1200px; height: 892px; overflow: hidden; }
  body {
    background: var(--page);
    display: flex;
    align-items: center;
    justify-content: center;
    gap: 44px;
  }
  .card {
    position: relative;
    width: 540px;
    height: 309px;
    border-radius: 3px;
    overflow: hidden;
    box-shadow: 0 6px 18px rgba(0,0,0,0.18);
  }

  /* Back: services */
  .card--back {
    background: linear-gradient(125deg, #1b1b1b 0%, #0b0b0b 40%, #2a2a2a 58%, #0a0a0a 75%, #141414 100%);
    color: var(--light-text);
  }
  .services__title {
    position: absolute;
    left: 74px;
    top: 30px;
    font-family: "Tinos", "Times New Roman", serif;
    font-size: 34px;
    font-weight: 400;
    letter-spacing: 0.5px;
  }
  .services__rule {
    position: absolute;
    left: 0;
    top: 84px;
    width: 300px;
    height: 1px;
    background: var(--light-rule);
  }
  .services__list {
    position: absolute;
    left: 54px;
    top: 116px;
    list-style: none;
    font-family: "Open Sans", Verdana, sans-serif;
    font-size: 20px;
    letter-spacing: 0.6px;
  }
  .services__list li {
    display: flex;
    align-items: center;
    gap: 20px;
    height: 42px;
  }
  .services__bullet { width: 11px; height: 11px; flex: none; }

  /* Front: contact */
  .card--front {
    background: linear-gradient(180deg, var(--paper) 0%, var(--paper-shade) 100%);
    color: var(--ink);
  }
  .firm-name {
    position: absolute;
    right: 26px;
    top: 26px;
    font-family: "Tinos", "Times New Roman", serif;
    font-size: 25px;
    font-weight: 400;
  }
  .attorney {
    position: absolute;
    left: 34px;
    top: 98px;
    width: 250px;
  }
  .attorney__name {
    font-family: "Tinos", "Times New Roman", serif;
    font-size: 30px;
    font-weight: 700;
    line-height: 1.05;
  }
  .attorney__title {
    margin-top: 4px;
    font-family: "Open Sans", Verdana, sans-serif;
    font-size: 14px;
    color: var(--muted);
  }
  .divider {
    position: absolute;
    left: 292px;
    top: 104px;
    width: 1px;
    height: 118px;
    background: var(--rule);
  }
  .contacts {
    position: absolute;
    left: 310px;
    top: 108px;
    list-style: none;
    font-family: "Open Sans", Verdana, sans-serif;
    font-size: 14.5px;
  }
  .contacts li {
    display: flex;
    align-items: center;
    gap: 10px;
    height: 28px;
  }
  .contacts__icon { width: 15px; height: 15px; flex: none; }
  .address-band {
    position: absolute;
    left: 0; right: 0; bottom: 0;
    height: 44px;
    background: var(--band);
    color: var(--light-text);
    font-family: "Open Sans", Verdana, sans-serif;
    font-size: 15px;
    letter-spacing: 0.3px;
    display: flex;
    align-items: center;
    padding-left: 34px;
  }
</style>
</head>
<body>

  <section class="card card--back" aria-label="Card back: services">
    <h2 class="services__title">Service</h2>
    <div class="services__rule"></div>
    <ul class="services__list">
      <li><svg class="services__bullet" viewBox="0 0 12 12"><circle cx="6" cy="6" r="4.5" fill="none" stroke="#bbb" stroke-width="1"/><circle cx="6" cy="6" r="1.6" fill="#ddd"/></svg>Civil Litigation</li>
      <li><svg class="services__bullet" viewBox="0 0 12 12"><circle cx="6" cy="6" r="4.5" fill="none" stroke="#bbb" stroke-width="1"/><circle cx="6" cy="6" r="1.6" fill="#ddd"/></svg>Corporate Law</li>
      <li><svg class="services__bullet" viewBox="0 0 12 12"><circle cx="6" cy="6" r="4.5" fill="none" stroke="#bbb" stroke-width="1"/><circle cx="6" cy="6" r="1.6" fill="#ddd"/></svg>Real Estate Law</li>
      <li><svg class="services__bullet" viewBox="0 0 12 12"><circle cx="6" cy="6" r="4.5" fill="none" stroke="#bbb" stroke-width="1"/><circle cx="6" cy="6" r="1.6" fill="#ddd"/></svg>Business Governance</li>
    </ul>
  </section>

  <section class="card card--front" aria-label="Card front: contact">
    <h1 class="firm-name">Law Offices of Colin Matheny, P.A.</h1>
    <div class="attorney">
      <div class="attorney__name">Colin Matheny</div>
      <div class="attorney__title">Attorney</div>
    </div>
    <div class="divider"></div>
    <ul class="contacts">
      <li>
        <svg class="contacts__icon" viewBox="0 0 16 16"><rect width="16" height="16" rx="2" fill="#111"/><path d="M5 3.5l2 2-1.2 1.3a6 6 0 0 0 3.4 3.4L10.5 9l2 2-1.3 1.6C7.5 12.3 3.7 8.5 3.4 4.8z" fill="#fff"/></svg>
        555-214-7390
      </li>
      <li>
        <svg class="contacts__icon" viewBox="0 0 16 16"><rect width="16" height="16" rx="2" fill="#111"/><rect x="5" y="2.5" width="6" height="11" rx="1" fill="#fff"/><rect x="6" y="4" width="4" height="6" fill="#111"/></svg>
        555-382-6418
      </li>
      <li>
        <svg class="contacts__icon" viewBox="0 0 16 16"><rect width="16" height="16" rx="2" fill="#111"/><circle cx="8" cy="8" r="5" fill="none" stroke="#fff" stroke-width="1.2"/><ellipse cx="8" cy="8" rx="2" ry="5" fill="none" stroke="#fff" stroke-width="1"/><line x1="3" y1="8" x2="13" y2="8" stroke="#fff" stroke-width="1"/></svg>
        www.mathenylegal.com
      </li>
      <li>
        <svg class="contacts__icon" viewBox="0 0 16 16"><rect width="16" height="16" rx="2" fill="#111"/><rect x="3" y="4.5" width="10" height="7" fill="#fff"/><path d="M3 4.5l5 4 5-4" fill="none" stroke="#111" stroke-width="1"/></svg>
        colin@mathenylegal.com
      </li>
    </ul>
    <div class="address-band">118 Harbor Lane Coral Bay, Florida 33999</div>
  </section>

</body>
</html>
```